Real estate agent website

I am a new real estate agent and in of a simple but powerful website that is linked to the local Multiple listing services (MLS). It should have a lending page that is connected to my customer relationship management (CRM) software. It must have an ability for potential customers to search for properties and be able to communicate with me easily.
Updates

Updates: The website themes must includes MLS-IDX integration with a grid layout and property slider so i can showcase featured properties. I also would like to have future where potential client can search and have alerts depending on a search criteria.

Industry/Entity Type

Real Estate

Coding

Coded - Design and coding required

Number of Pages Required

3 page

Requirements
Must have
• Home page, Resources page, About Me with contact me window page

```html
<!DOCTYPE html>
<html lang="en">
<head>
<meta charset="utf-8">
<title>Marina Hollis – Real Estate Agent</title>
<link href="https://fonts.googleapis.com/css2?family=Montserrat:wght@600;700&family=Roboto+Condensed:wght@300;400;500;700&display=swap" rel="stylesheet">
<style>
:root{
  --dark:#4a4d56;
  --orange:#d08c35;
  --teal:#3a8a80;
  --grey:#ebecf0;
  --text:#666a72;
  --heading:#3d4048;
  --white:#fff;
}
*{box-sizing:border-box;margin:0;padding:0}
html,body{width:1200px;height:3585px;overflow:hidden;background:#fff}
body{position:relative;font-family:"Roboto Condensed",Arial,sans-serif;color:var(--text)}
.btn{position:absolute;display:flex;align-items:center;justify-content:center;gap:7px;color:#fff;font-weight:700;text-transform:uppercase;font-size:14px;border-radius:2px;white-space:nowrap}
.btn--orange{background:var(--orange)}
.btn--teal{background:var(--teal)}

/* header */
.header{position:absolute;left:0;top:0;width:1200px;height:128px;background:#fff}
.header__brand{position:absolute;left:0;top:0;width:457px;height:128px;background:var(--dark);clip-path:polygon(0 0,100% 0,82% 100%,0 100%)}
.brand-name{position:absolute;font-family:"Roboto Condensed",sans-serif;font-weight:700;font-size:28px;letter-spacing:1px;color:#fff;white-space:nowrap}
.call{position:absolute;left:668px;top:22px;display:flex;align-items:center;gap:16px}
.call__icon{width:48px;height:48px;border-radius:50%;border:2px solid var(--teal);display:flex;align-items:center;justify-content:center}
.call__label{font-size:11px;font-weight:500;color:#666}
.call__num{font-size:16px;font-weight:500;color:#333}
.nav{position:absolute;right:111px;top:91px;display:flex;gap:25px;font-size:14px;font-weight:700;color:#444}
.nav .active{color:var(--orange)}

/* hero */
.hero{position:absolute;left:0;top:128px;width:1200px;height:600px;background:linear-gradient(100deg,#3b3127 0%,#4f5258 35%,#5b6470 60%,#3e4147 100%)}
.hero__shade{position:absolute;left:0;top:360px;width:1200px;height:240px;background:linear-gradient(180deg,rgba(120,70,40,0) 0%,rgba(110,65,35,.55) 100%)}
.hero__title{position:absolute;left:0;top:166px;width:1200px;text-align:center;font-family:Montserrat,sans-serif;font-weight:600;font-size:39px;line-height:49px;color:#fff}
.search{position:absolute;left:264px;top:298px;width:669px;height:109px;background:rgba(120,125,135,.45);border-radius:4px}
.search__box{position:absolute;left:51px;top:39px;width:569px;height:47px;background:#fff;border:2px solid #fff;display:flex;align-items:center}
.search__text{flex:1;display:flex;align-items:center;gap:8px;padding-left:14px;font-size:14px;color:#444}
.search__btn{position:static;width:99px;height:43px;font-size:14px}

/* about */
.about__photo{position:absolute;left:110px;top:827px;width:428px;height:428px;border-radius:50%;background:var(--teal)}
.about__photo-inner{position:absolute;left:12px;top:0;width:404px;height:404px;border-radius:50%;background:radial-gradient(circle at 50% 40%,#d9a88a 0%,#a27560 35%,#4a4848 75%)}
.h2{font-family:Montserrat,sans-serif;font-weight:700;color:var(--heading)}
.about__title{position:absolute;left:600px;top:826px;font-size:33px;line-height:43px}
.underline{position:absolute;height:4px;width:94px;background:var(--teal)}
.about__text{position:absolute;left:600px;top:956px;width:490px;font-size:15px;line-height:25.5px;font-weight:300;color:#555}
.about__text p{margin-bottom:9px}

/* listings */
.featured{position:absolute;left:0;top:1361px;width:1200px;height:1270px;background:var(--grey)}
.section-title{position:absolute;left:0;width:1200px;text-align:center;font-size:36px}
.card{position:absolute;width:309px;height:430px;background:#fff;box-shadow:0 2px 8px rgba(0,0,0,.08);border-radius:3px}
.card__img{position:absolute;left:7px;top:7px;width:295px;height:203px}
.card__title{position:absolute;left:20px;top:228px;font-size:16px;font-weight:700;color:#333;text-transform:uppercase}
.card__loc{position:absolute;left:20px;top:256px;font-size:13px;color:#555;display:flex;gap:6px;align-items:center}
.card__rule{position:absolute;left:20px;width:269px;height:1px;background:#e3e3e3}
.card__specs{position:absolute;left:20px;top:292px;width:269px;display:grid;grid-template-columns:170px 99px;row-gap:10px;font-size:11.5px;color:#777}
.spec{display:flex;align-items:center;gap:8px}
.spec__ico{width:15px;height:12px;border:1.5px solid #a5a5a5;border-radius:1px;flex:none}
.card__btn{left:20px;top:363px;width:113px;height:41px;font-size:12px}
.card__price{position:absolute;right:20px;top:372px;font-size:18px;font-weight:700;color:var(--teal)}

/* contact */
.field{position:absolute;background:#fff;box-shadow:0 1px 6px rgba(0,0,0,.12);font-size:14px;color:#666;padding:16px 17px}
.info{position:absolute;left:788px;width:400px}
.info__icon{position:absolute;left:0;width:80px;height:80px;border-radius:50%;border:2px solid var(--teal);background:#fff;box-shadow:0 2px 8px rgba(0,0,0,.12);display:flex;align-items:center;justify-content:center}
.info__label{position:absolute;left:108px;font-size:14px;font-weight:700;color:#333}
.info__value{position:absolute;left:108px;font-size:14px;line-height:20px;color:#666}

/* footer */
.footer{position:absolute;left:0;top:3252px;width:1200px;height:333px;background:var(--dark)}
.footer__brand{left:0;top:62px;width:1200px;text-align:center}
.footer__nav{position:absolute;top:140px;left:0;width:1200px;display:flex;justify-content:center;gap:16px;font-size:16px;font-weight:700;color:#fff}
.footer__nav span.sep{font-weight:400}
.footer__contact{position:absolute;top:178px;left:0;width:1200px;display:flex;justify-content:center;align-items:center;gap:14px;font-size:16px;color:#fff}
.social{position:absolute;top:216px;left:0;width:1200px;display:flex;justify-content:center;gap:5px}
.social span{width:30px;height:30px;border-radius:50%;border:1px solid #fff;display:block}
.social span.on{background:var(--orange);border-color:var(--orange)}
.footer__rule{position:absolute;left:111px;top:270px;width:978px;height:1px;background:#6c6f78}
.footer__copy{position:absolute;top:292px;left:0;width:1200px;text-align:center;font-size:12px;color:#fff}
</style>
</head>
<body>

<header class="header">
  <div class="header__brand"></div>
  <div class="brand-name" style="left:116px;top:44px">MARINA HOLLIS</div>
  <div class="call">
    <div class="call__icon">
      <svg width="22" height="22" viewBox="0 0 24 24"><path d="M6.6 10.8a15 15 0 0 0 6.6 6.6l2.2-2.2a1 1 0 0 1 1-.25 11.4 11.4 0 0 0 3.6.57 1 1 0 0 1 1 1V20a1 1 0 0 1-1 1A17 17 0 0 1 3 4a1 1 0 0 1 1-1h3.5a1 1 0 0 1 1 1c0 1.25.2 2.45.57 3.57a1 1 0 0 1-.25 1z" fill="var(--orange)"/></svg>
    </div>
    <div><div class="call__label">CALL US:</div><div class="call__num">612-555-0148</div></div>
  </div>
  <div class="btn btn--teal" style="left:868px;top:22px;width:105px;height:48px">
    <svg width="12" height="13" viewBox="0 0 12 13"><circle cx="6" cy="3.5" r="3" fill="#fff"/><path d="M0 13a6 5 0 0 1 12 0z" fill="#fff"/></svg>LOGIN</div>
  <div class="btn btn--orange" style="left:982px;top:22px;width:107px;height:48px">
    <svg width="12" height="13" viewBox="0 0 12 13"><circle cx="6" cy="3.5" r="3" fill="#fff"/><path d="M0 13a6 5 0 0 1 12 0z" fill="#fff"/></svg>SIGN UP</div>
  <nav class="nav">
    <span class="active">HOME</span><span>BUY/SELL</span><span>RENT</span><span>LENDING</span><span>LISTINGS</span><span>FIND REALTORS</span><span>CONTACT</span>
  </nav>
</header>

<section class="hero" role="img" aria-label="Modern living room with leather sofa, fireplace and wooden staircase">
  <div class="hero__shade"></div>
  <h1 class="hero__title">MARINA HOLLIS<br>REAL ESTATE AGENT</h1>
  <div class="search">
    <div class="search__box">
      <div class="search__text">
        <svg width="10" height="14" viewBox="0 0 10 14"><path d="M5 0a5 5 0 0 1 5 5c0 3.5-5 9-5 9S0 8.5 0 5a5 5 0 0 1 5-5z" fill="#333"/><circle cx="5" cy="5" r="2" fill="#fff"/></svg>
        Start your search by City, Zipcode
      </div>
      <div class="btn btn--orange search__btn">SEARCH</div>
    </div>
  </div>
</section>

<section class="about">
  <div class="about__photo"><div class="about__photo-inner" role="img" aria-label="Portrait of the agent"></div></div>
  <h2 class="h2 about__title">ABOUT<br>MARINA HOLLIS</h2>
  <div class="underline" style="left:600px;top:920px"></div>
  <div class="about__text">
    <p>Purchasing or selling a house is the biggest investment venture that most of us will have in our lifetime. A home is a place of comfort and love. It is where we create memories. A place to live with our families and pets and enjoy our friends, and it's a place where we create life-long memories.</p>
    <p>No matter what your goal or needs are in real estate, I would be honored to guide you through this journey. This is never just a business transaction; it will be a time where we would learn how to build trust</p>
  </div>
  <div class="btn btn--orange" style="left:600px;top:1175px;width:132px;height:48px">CONTACT NOW</div>
</section>

<section class="featured">
  <h2 class="h2 section-title" style="top:88px">FEATURED LISTINGS</h2>
  <div class="underline" style="left:553px;top:141px"></div>

  <article class="card" style="left:111px;top:194px">
    <div class="card__img" role="img" aria-label="Two-storey suburban home at dusk" style="background:linear-gradient(180deg,#8fa3c0 0%,#b9a58a 55%,#5f8a3a 80%)"></div>
    <h3 class="card__title">20418 Birchwood Avenue</h3>
    <div class="card__loc"><svg width="9" height="12" viewBox="0 0 10 14"><path d="M5 0a5 5 0 0 1 5 5c0 3.5-5 9-5 9S0 8.5 0 5a5 5 0 0 1 5-5z" fill="var(--teal)"/><circle cx="5" cy="5" r="2" fill="#fff"/></svg>Lakeville, MN 55044</div>
    <div class="card__rule" style="top:282px"></div>
    <div class="card__specs"><span class="spec"><i class="spec__ico"></i>3 Bedrooms</span><span class="spec"><i class="spec__ico"></i>4 Bathrooms</span><span class="spec"><i class="spec__ico"></i>2,361 Sqft</span><span class="spec"><i class="spec__ico"></i>2 Cars</span></div>
    <div class="card__rule" style="top:348px"></div>
    <div class="btn btn--orange card__btn">VIEW DETAILS</div>
    <div class="card__price">$330,000</div>
  </article>
  <article class="card" style="left:445px;top:194px">
    <div class="card__img" role="img" aria-label="Modern two-storey home with garage" style="background:linear-gradient(180deg,#9fb8d2 0%,#c9c6c0 50%,#6e9448 85%)"></div>
    <h3 class="card__title">13602 208th Street N</h3>
    <div class="card__loc"><svg width="9" height="12" viewBox="0 0 10 14"><path d="M5 0a5 5 0 0 1 5 5c0 3.5-5 9-5 9S0 8.5 0 5a5 5 0 0 1 5-5z" fill="var(--teal)"/><circle cx="5" cy="5" r="2" fill="#fff"/></svg>Scandia, MN 55073</div>
    <div class="card__rule" style="top:282px"></div>
    <div class="card__specs"><span class="spec"><i class="spec__ico"></i>3 Bedrooms</span><span class="spec"><i class="spec__ico"></i>4 Bathrooms</span><span class="spec"><i class="spec__ico"></i>3,508 Sqft</span><span class="spec"><i class="spec__ico"></i>2 Cars</span></div>
    <div class="card__rule" style="top:348px"></div>
    <div class="btn btn--orange card__btn">VIEW DETAILS</div>
    <div class="card__price">$849,900</div>
  </article>
  <article class="card" style="left:780px;top:194px">
    <div class="card__img" role="img" aria-label="Classic home with garden and front steps" style="background:linear-gradient(180deg,#4f7a3a 0%,#8c8f86 45%,#5e8c35 85%)"></div>
    <h3 class="card__title">15170 Alder Trail</h3>
    <div class="card__loc"><svg width="9" height="12" viewBox="0 0 10 14"><path d="M5 0a5 5 0 0 1 5 5c0 3.5-5 9-5 9S0 8.5 0 5a5 5 0 0 1 5-5z" fill="var(--teal)"/><circle cx="5" cy="5" r="2" fill="#fff"/></svg>Apple Valley, MN 55124</div>
    <div class="card__rule" style="top:282px"></div>
    <div class="card__specs"><span class="spec"><i class="spec__ico"></i>3 Bedrooms</span><span class="spec"><i class="spec__ico"></i>4 Bathrooms</span><span class="spec"><i class="spec__ico"></i>1,890 Sqft</span><span class="spec"><i class="spec__ico"></i>2 Cars</span></div>
    <div class="card__rule" style="top:348px"></div>
    <div class="btn btn--orange card__btn">VIEW DETAILS</div>
    <div class="card__price">$365,000</div>
  </article>

  <article class="card" style="left:111px;top:649px">
    <div class="card__img" role="img" aria-label="Contemporary home with stone path and lawn" style="background:linear-gradient(180deg,#cfd8e0 0%,#6f6760 45%,#5f9a3a 85%)"></div>
    <h3 class="card__title">418 Linden Street 210</h3>
    <div class="card__loc"><svg width="9" height="12" viewBox="0 0 10 14"><path d="M5 0a5 5 0 0 1 5 5c0 3.5-5 9-5 9S0 8.5 0 5a5 5 0 0 1 5-5z" fill="var(--teal)"/><circle cx="5" cy="5" r="2" fill="#fff"/></svg>Saint Paul, MN 55102</div>
    <div class="card__rule" style="top:282px"></div>
    <div class="card__specs"><span class="spec"><i class="spec__ico"></i>2 Bedrooms</span><span class="spec"><i class="spec__ico"></i>2 Bathrooms</span><span class="spec"><i class="spec__ico"></i>1,706 Sqft</span><span class="spec"><i class="spec__ico"></i>2 Cars</span></div>
    <div class="card__rule" style="top:348px"></div>
    <div class="btn btn--orange card__btn">VIEW DETAILS</div>
    <div class="card__price">$599,900</div>
  </article>
  <article class="card" style="left:445px;top:649px">
    <div class="card__img" role="img" aria-label="Craftsman home with porch at dusk" style="background:linear-gradient(180deg,#2f3f58 0%,#7a7d82 50%,#3f6b2c 85%)"></div>
    <h3 class="card__title">2730 Fernview Court</h3>
    <div class="card__loc"><svg width="9" height="12" viewBox="0 0 10 14"><path d="M5 0a5 5 0 0 1 5 5c0 3.5-5 9-5 9S0 8.5 0 5a5 5 0 0 1 5-5z" fill="var(--teal)"/><circle cx="5" cy="5" r="2" fill="#fff"/></svg>Monticello, MN 55362</div>
    <div class="card__rule" style="top:282px"></div>
    <div class="card__specs"><span class="spec"><i class="spec__ico"></i>3 Bedrooms</span><span class="spec"><i class="spec__ico"></i>4 Bathrooms</span><span class="spec"><i class="spec__ico"></i>2,560 Sqft</span><span class="spec"><i class="spec__ico"></i>2 Cars</span></div>
    <div class="card__rule" style="top:348px"></div>
    <div class="btn btn--orange card__btn">VIEW DETAILS</div>
    <div class="card__price">$339,900</div>
  </article>
  <article class="card" style="left:780px;top:649px">
    <div class="card__img" role="img" aria-label="Farmhouse with lit windows at sunset" style="background:linear-gradient(180deg,#c98a8f 0%,#d8d2c8 45%,#5e8a38 85%)"></div>
    <h3 class="card__title">13410 309th Avenue</h3>
    <div class="card__loc"><svg width="9" height="12" viewBox="0 0 10 14"><path d="M5 0a5 5 0 0 1 5 5c0 3.5-5 9-5 9S0 8.5 0 5a5 5 0 0 1 5-5z" fill="var(--teal)"/><circle cx="5" cy="5" r="2" fill="#fff"/></svg>Baldwin Twp, MN 55371</div>
    <div class="card__rule" style="top:282px"></div>
    <div class="card__specs"><span class="spec"><i class="spec__ico"></i>3 Bedrooms</span><span class="spec"><i class="spec__ico"></i>4 Bathrooms</span><span class="spec"><i class="spec__ico"></i>1,968 Sqft</span><span class="spec"><i class="spec__ico"></i>2 Cars</span></div>
    <div class="card__rule" style="top:348px"></div>
    <div class="btn btn--orange card__btn">VIEW DETAILS</div>
    <div class="card__price">$399,900</div>
  </article>

  <div class="btn btn--teal" style="left:516px;top:1128px;width:167px;height:47px">VIEW ALL LISTINGS</div>
</section>

<section class="contact">
  <h2 class="h2 section-title" style="top:2738px">GET IN TOUCH</h2>
  <div class="underline" style="left:553px;top:2791px"></div>

  <div class="field" style="left:150px;top:2838px;width:282px;height:49px">First Name</div>
  <div class="field" style="left:445px;top:2838px;width:282px;height:49px">Last Name</div>
  <div class="field" style="left:150px;top:2901px;width:282px;height:49px">Phone Number</div>
  <div class="field" style="left:445px;top:2901px;width:282px;height:49px">Email</div>
  <div class="field" style="left:150px;top:2965px;width:577px;height:110px">Message</div>
  <div class="btn btn--orange" style="left:150px;top:3090px;width:161px;height:46px;font-size:15px">SEND MESSAGE</div>

  <div class="info" style="top:2837px">
    <div class="info__icon" style="top:0">
      <svg width="34" height="34" viewBox="0 0 34 34"><path d="M17 3a8 8 0 0 1 8 8c0 6-8 14-8 14s-8-8-8-14a8 8 0 0 1 8-8z" fill="none" stroke="var(--orange)" stroke-width="2.2"/><circle cx="17" cy="11" r="3" fill="var(--orange)"/><ellipse cx="17" cy="28" rx="11" ry="3" fill="none" stroke="var(--orange)" stroke-width="2"/></svg>
    </div>
    <div class="info__label" style="top:6px">ADDRESS:</div>
    <div class="info__value" style="top:32px">4120 CEDAR RIDGE RD STE 110,<br>MAPLE GROVE, MN, 55369</div>
  </div>
  <div class="info" style="top:2940px">
    <div class="info__icon" style="top:0">
      <svg width="30" height="30" viewBox="0 0 24 24"><path d="M6.6 10.8a15 15 0 0 0 6.6 6.6l2.2-2.2a1 1 0 0 1 1-.25 11.4 11.4 0 0 0 3.6.57 1 1 0 0 1 1 1V20a1 1 0 0 1-1 1A17 17 0 0 1 3 4a1 1 0 0 1 1-1h3.5a1 1 0 0 1 1 1c0 1.250.2 2.45.57 3.570a1 1 0 0 1-.25 1z" fill="var(--orange)"/></svg>
    </div>
    <div class="info__label" style="top:18px">PHONE:</div>
    <div class="info__value" style="top:44px">(612) 555-0148</div>
  </div>
  <div class="info" style="top:3043px">
    <div class="info__icon" style="top:0">
      <svg width="36" height="26" viewBox="0 0 36 26"><rect x="0" y="0" width="36" height="26" rx="2" fill="var(--orange)"/><path d="M2 3l16 12L34 3" fill="none" stroke="#fff" stroke-width="2.5"/></svg>
    </div>
    <div class="info__label" style="top:18px">EMAIL:</div>
    <div class="info__value" style="top:44px">mhollis.realtor@example.com</div>
  </div>
</section>

<footer class="footer">
  <div class="brand-name footer__brand">MARINA HOLLIS</div>
  <nav class="footer__nav">
    <span>HOME</span><span class="sep">|</span><span>BUY/SELL</span><span class="sep">|</span><span>RENT</span><span class="sep">|</span><span>LENDING</span><span class="sep">|</span><span>LISTINGS</span><span class="sep">|</span><span>FIND REALTORS</span><span class="sep">|</span><span>CONTACT US</span>
  </nav>
  <div class="footer__contact">
    <svg width="14" height="14" viewBox="0 0 24 24"><path d="M6.6 10.8a15 15 0 0 0 6.6 6.6l2.2-2.2a1 1 0 0 1 1-.25 11.4 11.4 0 0 0 3.6.57 1 1 0 0 1 1 1V20a1 1 0 0 1-1 1A17 17 0 0 1 3 4a1 1 0 0 1 1-1h3.5a1 1 0 0 1 1 1c0 1.25.2 2.45.57 3.57a1 1 0 0 1-.25 1z" fill="var(--teal)"/></svg>
    <span>612-555-0148</span><span style="margin:0 6px">|</span>
    <svg width="16" height="12" viewBox="0 0 36 26"><rect width="36" height="26" rx="2" fill="var(--teal)"/><path d="M2 3l16 12L34 3" fill="none" stroke="var(--dark)" stroke-width="3"/></svg>
    <span>mhollis.realtor@example.com</span>
  </div>
  <div class="social"><span class="on"></span><span></span><span></span><span></span></div>
  <div class="footer__rule"></div>
  <div class="footer__copy">© 2023 <b>MARINA HOLLIS</b> &nbsp;|&nbsp; Alle rechten voorbehouden</div>
</footer>

</body>
</html>
```